Working Capital graphics

Our business advisory firm requires 9 images to be re-created and improved in the branding of our business.

The 9 images have been uploaded below and the colours and branding of the business can be found at the website www.tallowmereadvisory.com.au

```html
<!DOCTYPE html>
<html lang="en">
<head>
<meta charset="utf-8">
<title>Net Working Capital Absorption</title>
<link rel="stylesheet" href="https://fonts.googleapis.com/css2?family=Montserrat:wght@500;600;700&display=swap">
<style>
  :root {
    --navy: #1b2a50;
    --sky: #66c7f2;
    --axis-grey: #8c8c8c;
    --label-grey: #9a9a9a;
    --accent-orange: #f7941d;
    --paper: #ffffff;
  }
  html, body {
    margin: 0;
    padding: 0;
    width: 1200px;
    height: 1134px;
    overflow: hidden;
    background: var(--paper);
  }
  .chart {
    display: block;
    width: 1200px;
    height: 1134px;
    font-family: "Montserrat", sans-serif;
  }
  .chart-title { fill: var(--navy); font-size: 39px; font-weight: 600; letter-spacing: 1px; }
  .axis-line { stroke: var(--axis-grey); stroke-width: 2; }
  .tick-label { fill: var(--label-grey); font-size: 22px; font-weight: 600; }
  .axis-title { fill: var(--accent-orange); font-size: 22px; font-weight: 600; letter-spacing: 1px; }
  .guide-line { stroke: var(--navy); stroke-width: 1.5; stroke-dasharray: 6 5; }
  .zone { fill: var(--sky); }
  .vector { stroke: var(--navy); stroke-width: 2.5; fill: none; }
  .origin { fill: var(--navy); }
  .arrow-head { fill: var(--navy); }
  .vector-letter { fill: var(--navy); font-size: 38px; font-weight: 600; }
  .vector-name { fill: var(--navy); font-size: 22px; font-weight: 600; letter-spacing: 0.5px; }
</style>
</head>
<body>
<svg class="chart" viewBox="0 0 1270 1200" xmlns="http://www.w3.org/2000/svg" role="img" aria-label="Net working capital absorption chart">
  <defs>
    <marker id="arrowhead" viewBox="0 0 12 12" refX="10" refY="6" markerWidth="7" markerHeight="7" orient="auto" markerUnits="strokeWidth">
      <path class="arrow-head" d="M0,0 L12,6 L0,12 L3,6 Z"/>
    </marker>
  </defs>

  <text class="chart-title" x="632" y="109" text-anchor="middle" dominant-baseline="central">NET WORKING CAPITAL ABSORPTION</text>

  <g class="axes">
    <line class="axis-line" x1="321" y1="262" x2="321" y2="975"/>
    <line class="axis-line" x1="320" y1="974" x2="1020" y2="974"/>
  </g>

  <g class="y-ticks" text-anchor="end" dominant-baseline="central">
    <text class="tick-label" x="300" y="280">450m</text>
    <text class="tick-label" x="300" y="374">400m</text>
    <text class="tick-label" x="300" y="468">350m</text>
    <text class="tick-label" x="300" y="562">300m</text>
    <text class="tick-label" x="300" y="656">250m</text>
    <text class="tick-label" x="300" y="749">200m</text>
    <text class="tick-label" x="300" y="843">150m</text>
    <text class="tick-label" x="300" y="937">100m</text>
  </g>

  <g class="x-ticks" text-anchor="middle" dominant-baseline="central">
    <text class="tick-label" x="384" y="1007">20m</text>
    <text class="tick-label" x="497" y="1007">25m</text>
    <text class="tick-label" x="608" y="1007">30m</text>
    <text class="tick-label" x="720" y="1007">35m</text>
    <text class="tick-label" x="832" y="1007">40m</text>
    <text class="tick-label" x="944" y="1007">45m</text>
  </g>

  <text class="axis-title" x="175" y="617" text-anchor="middle" dominant-baseline="central" transform="rotate(-90 175 617)">SALES</text>
  <text class="axis-title" x="675" y="1070" text-anchor="middle" dominant-baseline="central">NET WORKING CAPITAL (NWC)</text>

  <circle class="zone" cx="675" cy="611" r="220"/>

  <g class="guides">
    <line class="guide-line" x1="322" y1="611" x2="675" y2="611"/>
    <line class="guide-line" x1="675" y1="611" x2="675" y2="973"/>
  </g>

  <g class="vectors" marker-end="url(#arrowhead)">
    <line class="vector" x1="675" y1="611" x2="510" y2="433" marker-end="url(#arrowhead)"/>
    <line class="vector" x1="675" y1="611" x2="675" y2="343" marker-end="url(#arrowhead)"/>
    <line class="vector" x1="675" y1="611" x2="821" y2="399" marker-end="url(#arrowhead)"/>
    <line class="vector" x1="675" y1="611" x2="929" y2="611" marker-end="url(#arrowhead)"/>
    <line class="vector" x1="675" y1="611" x2="827" y2="792" marker-end="url(#arrowhead)"/>
    <line class="vector" x1="675" y1="611" x2="472" y2="772" marker-end="url(#arrowhead)"/>
  </g>

  <circle class="origin" cx="675" cy="611" r="11"/>

  <g class="vector-letters" text-anchor="middle" dominant-baseline="central">
    <text class="vector-letter" x="489" y="407">A</text>
    <text class="vector-letter" x="675" y="309">B</text>
    <text class="vector-letter" x="839" y="372">C</text>
    <text class="vector-letter" x="958" y="611">D</text>
    <text class="vector-letter" x="845" y="818">E</text>
    <text class="vector-letter" x="456" y="797">F</text>
  </g>

  <g class="vector-names" dominant-baseline="central">
    <text class="vector-name" x="490" y="341" text-anchor="middle">OPTIMAL</text>
    <text class="vector-name" x="490" y="364" text-anchor="middle">GROWTH</text>
    <text class="vector-name" x="839" y="305" text-anchor="middle">FAST</text>
    <text class="vector-name" x="839" y="328" text-anchor="middle">GROWTH</text>
    <text class="vector-name" x="991" y="600">DECLINING</text>
    <text class="vector-name" x="991" y="623">GROWTH</text>
    <text class="vector-name" x="876" y="807">CORPORATE</text>
    <text class="vector-name" x="876" y="830">STRESS</text>
    <text class="vector-name" x="456" y="841" text-anchor="middle">DOWNSIZING</text>
  </g>
</svg>
</body>
</html>
```